BrindleStaffing Business Card Design

We are a staffing company finding positions for dedicated nurses and physicians.

Target Market(s)

Business Professionals

Industry/Entity Type

Staffing

Contact Information for Business Card

Gordon Pratley
Chairman
417 39th Avenue South
SAINT PETERSBURG FL 33712
813-555-4172 Mobile
813-555-8036 Fax
gpratley@brindlestaffing.com
www.brindlestaffing.com

Font styles to use
Sans Serif

Colors
fbee3e
f04a50
f37122

Requirements
Must have
• Logo Attached, see colors below. We'd like to see Yellow, Orange and Red.

```html
<!DOCTYPE html>
<html lang="en">
<head>
<meta charset="utf-8">
<title>BrindleStaffing Business Card</title>
<link href="https://fonts.googleapis.com/css2?family=Poppins:wght@400;500;700&display=swap" rel="stylesheet">
<style>
  :root {
    --stage: #e4e4e4;
    --brand-yellow: #fbee3e;
    --brand-orange: #f37122;
    --brand-red: #f04a50;
    --ink: #2b2b2b;
    --paper: #ffffff;
  }
  * { box-sizing: border-box; margin: 0; padding: 0; }
  html, body {
    width: 1200px; height: 895px; overflow: hidden;
    background: var(--stage);
    font-family: "Poppins", sans-serif;
  }
  .stage {
    width: 1200px; height: 895px;
    display: flex; flex-direction: column; align-items: center; justify-content: center;
    gap: 31px;
  }
  .card {
    position: relative;
    width: 700px; height: 400px;
    border-radius: 26px;
    overflow: hidden;
    box-shadow: 0 4px 14px rgba(0,0,0,0.18);
  }

  /* Front side */
  .card--front { background: var(--brand-orange); color: var(--paper); }
  .front-wordmark {
    position: absolute; left: 0; right: 0; top: 140px;
    text-align: center;
    font-weight: 700; font-size: 64px; letter-spacing: -1px;
  }
  .front-web {
    position: absolute; left: 0; right: 0; top: 250px;
    display: flex; align-items: center; gap: 16px;
  }
  .front-web .rule { flex: 1; height: 1px; background: rgba(255,255,255,0.85); }
  .front-web .url { font-size: 15px; letter-spacing: 2.5px; font-weight: 400; }

  /* Back side */
  .card--back { background: var(--paper); color: var(--ink); }
  .back-logo {
    position: absolute; left: 46px; top: 176px;
    display: flex; align-items: center; gap: 10px;
  }
  .back-logo .dot { width: 16px; height: 16px; border-radius: 50%; background: var(--brand-yellow); }
  .back-logo .name {
    font-weight: 700; font-size: 38px; letter-spacing: -0.5px; color: var(--brand-orange);
  }
  .divider { position: absolute; left: 392px; width: 2px; }
  .divider--yellow { top: 88px; height: 48px; background: var(--brand-yellow); }
  .divider--orange { top: 160px; height: 38px; background: var(--brand-orange); }
  .divider--red { top: 222px; height: 90px; background: var(--brand-red); }

  .contact { position: absolute; left: 418px; top: 82px; }
  .contact .person { font-weight: 700; font-size: 27px; color: var(--brand-red); line-height: 1.1; }
  .contact .role { font-size: 15px; margin-top: 2px; }
  .contact .address { font-size: 15px; line-height: 1.35; margin-top: 22px; }
  .contact .lines { list-style: none; margin-top: 22px; }
  .contact .lines li {
    display: flex; align-items: center; gap: 10px;
    font-size: 15px; line-height: 1.55;
  }
  .contact .lines svg { width: 13px; height: 13px; fill: var(--brand-orange); flex: none; }
  .contact .lines .label { color: #777; font-size: 13px; }
</style>
</head>
<body>
<main class="stage">
  <section class="card card--front" aria-label="Card front">
    <div class="front-wordmark">BrindleStaffing</div>
    <div class="front-web">
      <span class="rule"></span>
      <span class="url">www.brindlestaffing.com</span>
      <span class="rule"></span>
    </div>
  </section>

  <section class="card card--back" aria-label="Card back">
    <div class="back-logo">
      <span class="dot"></span>
      <span class="name">BrindleStaffing</span>
    </div>

    <span class="divider divider--yellow"></span>
    <span class="divider divider--orange"></span>
    <span class="divider divider--red"></span>

    <div class="contact">
      <div class="person">Gordon Pratley</div>
      <div class="role">Chairman</div>
      <div class="address">417 39th Avenue South<br>SAINT PETERSBURG FL 33712</div>
      <ul class="lines">
        <li>
          <svg viewBox="0 0 24 24" aria-hidden="true"><path d="M6.6 10.8a15.1 15.1 0 0 0 6.6 6.6l2.2-2.2c.3-.3.7-.4 1-.2 1.1.4 2.3.6 3.6.6.6 0 1 .4 1 1V20c0 .6-.4 1-1 1C10.6 21 3 13.4 3 4c0-.6.4-1 1-1h3.5c.6 0 1 .4 1 1 0 1.3.2 2.5.6 3.6.1.3 0 .7-.2 1z"/></svg>
          813-555-4172 <span class="label">Mobile</span>
        </li>
        <li>
          <svg viewBox="0 0 24 24" aria-hidden="true"><path d="M6 2h12v6H6z M3 9h18v9h-3v4H6v-4H3z M8 15v5h8v-5z"/></svg>
          813-555-8036 <span class="label">Fax</span>
        </li>
        <li>
          <svg viewBox="0 0 24 24" aria-hidden="true"><path d="M2 5h20v14H2V5zm2 2v.3l8 6 8-6V7l-8 6-8-6z"/></svg>
          gpratley@brindlestaffing.com
        </li>
        <li>
          <svg viewBox="0 0 24 24" aria-hidden="true"><path d="M12 2a10 10 0 1 0 0 20 10 10 0 0 0 0-20zm6.9 9h-3a15 15 0 0 0-1.3-5.6A8 8 0 0 1 18.9 11zM12 4.1c.9 1.3 1.8 3.8 1.9 6.9h-3.8c.1-3.1 1-5.6 1.9-6.9zM9.4 5.4A15 15 0 0 0 8.1 11h-3a8 8 0 0 1 4.3-5.6zM5.1 13h3a15 15 0 0 0 1.3 5.6A8 8 0 0 1 5.1 13zM12 19.9c-.9-1.3-1.8-3.8-1.9-6.9h3.8c-.1 3.1-1 5.6-1.9 6.9zm2.6-1.3a15 15 0 0 0 1.3-5.6h3a8 8 0 0 1-4.3 5.6z"/></svg>
          www.brindlestaffing.com
        </li>
      </ul>
    </div>
  </section>
</main>
</body>
</html>
```